Card design for orthopaedic surgeons working as The Brightwater Joint Centre

Business cards, letterhead

Colors

Designer to choose colors to be used in the design.

Requirements
Must have
• Late addition.
• Cards letterhead must have logos of
• Crestmoor Lindell College of Surgeons
• Varenwood Bone Health Association
Nice to have
• Back of card to have space for appointment time to be added by hand and some blank space for writing incidental other notes.

```html
<!DOCTYPE html>
<html lang="en">
<head>
<meta charset="utf-8">
<title>The Brightwater Joint Centre – Stationery</title>
<link rel="stylesheet" href="https://fonts.googleapis.com/css2?family=Montserrat:wght@400;500;600&family=Arimo:wght@400;700&display=swap">
<style>
  :root{
    --navy:#0d3349;
    --sky:#5a9fd4;
    --paper:#f5f5f5;
    --ink:#1e1e1e;
    --backdrop:#e4e4e4;
    --badge-warm:#c9a36a;
    --badge-cool:#9aa6b4;
  }
  *{margin:0;padding:0;box-sizing:border-box}
  html,body{width:1200px;height:1200px;overflow:hidden}
  body{background:radial-gradient(circle at 50% 55%,#ededed,var(--backdrop));position:relative;font-family:"Arimo",Arial,sans-serif;color:var(--ink)}
  .sheet{position:absolute;background:var(--paper);box-shadow:2px 3px 6px rgba(0,0,0,.35);overflow:hidden}
  .wave{position:absolute;left:0;top:0;width:100%}
  .brand{font-family:"Montserrat",sans-serif;font-weight:400;color:var(--navy);position:absolute;white-space:nowrap;letter-spacing:-.2px}
  .badge{position:absolute;border-radius:6px}
  .badge--college{background:linear-gradient(180deg,var(--badge-warm),#b04a3a)}
  .badge--association{background:linear-gradient(180deg,var(--badge-cool),#5f6f86)}

  /* Letterhead */
  .letterhead{left:98px;top:124px;width:678px;height:956px}
  .letterhead .contact{position:absolute;right:32px;top:25px;text-align:right;font-family:"Montserrat",sans-serif;font-size:10px;line-height:12.5px;color:#fff;letter-spacing:.2px}
  .letterhead .contact .gap{margin-top:4px}
  .icon{display:inline-block;vertical-align:-1px;margin-left:3px}
  .letterhead .brand{left:48px;top:75px;font-size:18.5px}
  .letter{position:absolute;left:48px;top:220px;width:584px;font-size:10.1px;line-height:13.7px}
  .letter .date{margin-bottom:13px}
  .letter .salutation{font-weight:700;margin:27px 0 27px}
  .letter p.body{text-align:justify;margin-bottom:13.7px}
  .letter .closing{margin-top:35px}
  .signature{width:162px;height:24px;margin:16px 0 12px;background:linear-gradient(90deg,rgba(30,30,30,.18),rgba(30,30,30,.08));border-radius:3px}
  .letterhead .site{position:absolute;left:48px;top:905px;font-family:"Montserrat",sans-serif;font-size:9.5px;letter-spacing:2.6px;color:var(--navy)}
  .site .accent{color:var(--sky)}
  .letterhead .badge--college{left:483px;top:857px;width:60px;height:69px}
  .letterhead .badge--association{left:562px;top:862px;width:66px;height:64px}

  /* Cards */
  .card{width:291px;height:177px;left:824px}
  .card--appointment{top:276px}
  .card--profile{top:505px}
  .card .heading{position:absolute;left:24px;top:18px;font-family:"Montserrat",sans-serif;font-weight:600;font-size:10px;color:var(--sky)}
  .field{position:absolute;left:21px;width:249px;font-family:"Montserrat",sans-serif;font-size:7.5px;color:var(--navy);display:flex;align-items:flex-end}
  .field .line{flex:1;border-bottom:.8px solid var(--sky);margin-left:9px;height:8px;position:relative}
  .field .time{position:absolute;left:131px;bottom:0}
  .card .web{position:absolute;left:0;width:100%;top:151px;text-align:center;font-family:"Montserrat",sans-serif;font-size:7.5px;color:var(--navy)}
  .card--profile .person{position:absolute;right:15px;top:15px;text-align:right;font-family:"Montserrat",sans-serif;color:#fff}
  .person .name{font-size:10px;font-weight:600;color:var(--sky)}
  .person .role{font-size:7.5px}
  .card--profile .brand{left:19px;top:53px;font-size:11px}
  .card--profile .details{position:absolute;left:19px;top:102px;font-family:"Montserrat",sans-serif;font-size:7.4px;line-height:9.6px;color:var(--navy)}
  .details .gap{margin-top:8px}
  .card--profile .badge--college{left:187px;top:118px;width:32px;height:40px;border-radius:4px}
  .card--profile .badge--association{left:233px;top:120px;width:42px;height:38px;border-radius:4px}
</style>
</head>
<body>

<section class="sheet letterhead">
  <svg class="wave" viewBox="0 0 1092 200" aria-hidden="true">
    <path fill="#5a9fd4" d="M0,62 C160,8 340,10 520,60 C720,118 900,168 1092,150 V196 C900,202 720,150 520,88 C340,34 160,30 0,80 Z"/>
    <path fill="#0d3349" d="M0,0 H1092 V150 C900,168 720,118 520,62 C340,14 160,16 0,66 Z"/>
    <path fill="none" stroke="#5a9fd4" stroke-width="5" d="M0,40 C180,0 360,10 490,68"/>
  </svg>
  <div class="contact">
    <div>48 Larkspur Row</div>
    <div>Fairhaven, 20417</div>
    <div class="gap">(555) 014-2290 <svg class="icon" width="8" height="8" viewBox="0 0 10 10"><path fill="#5a9fd4" d="M2,0.5 L3.8,2.8 L2.9,4 C3.6,5.4 4.6,6.4 6,7.1 L7.2,6.2 L9.5,8 L8.2,9.5 C4.5,9.3 0.7,5.5 0.5,1.8 Z"/></svg></div>
    <div>daniel@brightwaterjoint.com <svg class="icon" width="8" height="7" viewBox="0 0 10 8"><rect x=".5" y=".5" width="9" height="7" fill="none" stroke="#5a9fd4"/><path d="M.5,.5 L5,4.5 L9.5,.5" fill="none" stroke="#5a9fd4"/></svg></div>
  </div>
  <div class="brand">The Brightwater Joint Centre</div>

  <article class="letter">
    <div class="date">November 12, 2019</div>
    <address style="font-style:normal">
      Mr. Peter Lane<br>President<br>Ardent Holdings<br>111 Street Name, Suite#<br>City, State, 12345
    </address>
    <div class="salutation">Dear Mr. Peter,</div>
    <p class="body">Lorem ipsum dolor sit amet, consectetur adipiscing elit. Integer diam quam, egestas eu ultrices eu, suscipit ac sapien. Phasellus eu dui nisi. Nam et euismod diam, nec lobortis tortor. Donec et diam nulla. Aenean varius tincidunt convallis. Aliquam a tortor at lacus dictum aliquet. Nunc laoreet metus sapien, in scelerisque augue consectetur in.</p>
    <p class="body">Fusce nec justo laoreet, egestas justo sed, aliquet sem. Pellentesque pharetra massa non orci bibendum semper. Pellentesque cursus eu lectus a consectetur. Nunc volutpat suscipit posuere. Vestibulum facilisis vel quam malesuada mattis. Nulla in mattis tellus. Maecenas tristique mauris vitae pharetra tincidunt. In ut ornare risus. Integer molestie vestibulum nisi, semper dapibus mi condimentum eu.</p>
    <p class="body">Nullam sagittis elit libero, id fringilla est tincidunt eget. Donec in ipsum ultricies, consectetur quam vel, facilisis elit. Phasellus tincidunt congue risus vel luctus. Suspendisse ut mollis neque. Donec ornare orci in turpis vestibulum, in ultrices metus scelerisque. Pellentesque mattis mattis nunc, nec tincidunt lacus egestas id. Fusce facilisis sagittis neque sit amet vulputate. Aliquam ut eros lobortis tortor facilisis vehicula. Sed sed luctus leo, at laoreet sapien. Donec placerat adipiscing ligula non euismod. In lobortis pretium nisl id luctus.</p>
    <p class="body">Integer gravida tincidunt nibh, scelerisque tincidunt turpis. Suspendisse potenti. Nunc hendrerit euismod lectus id elementum. Fusce vitae gravida velit, quis eleifend lectus. In imperdiet mauris eu dui viverra sagittis. Donec tempor dui diam, condimentum gravida lacus pretium a. Nullam fringilla augue quis arcu placerat scelerisque. Aliquam nec tincidunt augue, sit amet posuere ipsum.</p>
    <div class="closing">Sincerely Yours,</div>
    <div class="signature" role="img" aria-label="Handwritten signature of Daniel Harrow"></div>
    <div>Daniel Harrow<br>Managing Director</div>
  </article>

  <div class="site">www.<span class="accent">brightwaterjoint</span>.com</div>
  <div class="badge badge--college" role="img" aria-label="Crestmoor Lindell College of Surgeons badge"></div>
  <div class="badge badge--association" role="img" aria-label="Varenwood Bone Health Association badge"></div>
</section>

<section class="sheet card card--appointment">
  <svg class="wave" viewBox="0 0 469 120" aria-hidden="true">
    <path fill="#5a9fd4" d="M0,92 C120,100 210,70 300,38 C370,14 420,4 469,20 V36 C420,22 370,30 300,56 C210,88 120,112 0,112 Z"/>
    <path fill="#0d3349" d="M0,0 H469 V22 C420,6 370,16 300,40 C210,72 120,100 0,94 Z"/>
    <path fill="none" stroke="#5a9fd4" stroke-width="4" d="M260,44 C340,12 410,0 469,12"/>
  </svg>
  <div class="heading">Next Appointment</div>
  <div class="field" style="top:78px">Name<span class="line"></span></div>
  <div class="field" style="top:104px">Date<span class="line"><span class="time">Time</span></span></div>
  <div class="field" style="top:130px">Note<span class="line"></span></div>
  <div class="web">www.brightwaterjoint.com</div>
</section>

<section class="sheet card card--profile">
  <svg class="wave" viewBox="0 0 469 120" aria-hidden="true">
    <path fill="#5a9fd4" d="M0,26 C110,2 210,10 300,50 C370,80 420,92 469,88 V108 C420,110 370,100 300,68 C210,30 110,22 0,40 Z"/>
    <path fill="#0d3349" d="M0,0 H469 V90 C420,94 370,84 300,52 C210,12 110,4 0,28 Z"/>
    <path fill="none" stroke="#5a9fd4" stroke-width="4" d="M0,16 C90,0 170,4 230,30"/>
  </svg>
  <div class="person">
    <div class="name">Daniel Harrow</div>
    <div class="role">Managing Director</div>
  </div>
  <div class="brand">The Brightwater Joint Centre</div>
  <div class="details">
    <div>48 Larkspur Row</div>
    <div>Fairhaven, 20417</div>
    <div class="gap"><svg class="icon" style="margin:0 3px 0 0" width="7" height="7" viewBox="0 0 10 10"><path fill="#5a9fd4" d="M2,0.5 L3.8,2.8 L2.9,4 C3.6,5.4 4.6,6.4 6,7.1 L7.2,6.2 L9.5,8 L8.2,9.5 C4.5,9.3 0.7,5.5 0.5,1.8 Z"/></svg>(555) 014-2290</div>
    <div><svg class="icon" style="margin:0 3px 0 0" width="7" height="6" viewBox="0 0 10 8"><rect x=".5" y=".5" width="9" height="7" fill="none" stroke="#5a9fd4"/><path d="M.5,.5 L5,4.5 L9.5,.5" fill="none" stroke="#5a9fd4"/></svg>daniel@brightwaterjoint.com</div>
    <div><svg class="icon" style="margin:0 3px 0 0" width="7" height="7" viewBox="0 0 10 10"><circle cx="5" cy="5" r="4.3" fill="none" stroke="#5a9fd4"/><path d="M.7,5 H9.3 M5,.7 C2.5,3.5 2.5,6.5 5,9.3 C7.5,6.5 7.5,3.5 5,.7" fill="none" stroke="#5a9fd4" stroke-width=".8"/></svg>www.brightwaterjoint.com</div>
  </div>
  <div class="badge badge--college" role="img" aria-label="Crestmoor Lindell College of Surgeons badge"></div>
  <div class="badge badge--association" role="img" aria-label="Varenwood Bone Health Association badge"></div>
</section>

</body>
</html>
```